Velmora Freightway Solutions Business cards

Would like a very unique design catchy but professional for business cards. Please use log provided.Marlon WellsCeo and Founder TransCon Logistix Solutions1-888-913-3225mwells@tlsolutionsus.comwww.tlsolutionsus.com

```html
<!DOCTYPE html>
<html lang="en">
<head>
<meta charset="utf-8">
<title>Velmora Freightway Solutions – Business Cards</title>
<link rel="stylesheet" href="https://fonts.googleapis.com/css2?family=Lato:wght@400;700&display=swap">
<style>
  :root {
    --stage: #3a3431;
    --paper: #f6f6f4;
    --brand-blue: #1170bb;
    --brand-red: #ee1c25;
    --ink: #4a4a4a;
    --rule: #b9cde3;
    --white: #ffffff;
  }
  * { margin: 0; padding: 0; box-sizing: border-box; }
  html, body {
    width: 1200px; height: 844px; overflow: hidden;
    background: var(--stage);
    font-family: "Lato", Arial, sans-serif;
  }
  .card-set {
    position: relative; width: 1200px; height: 844px;
    display: flex; align-items: center; justify-content: center; gap: 50px;
  }
  .card {
    position: relative; width: 525px; height: 300px;
    box-shadow: 0 8px 24px rgba(0,0,0,.45);
    overflow: hidden;
  }
  /* Front */
  .card--front { background: var(--paper); }
  .brand-lockup {
    position: absolute; top: 62px; right: 40px;
    display: flex; align-items: center; gap: 10px;
  }
  .brand-lockup__square {
    width: 22px; height: 22px; background: var(--brand-red);
  }
  .brand-lockup__name {
    font-weight: 700; font-size: 21px; letter-spacing: .6px;
    color: var(--brand-blue); text-transform: uppercase;
  }
  .divider {
    position: absolute; top: 128px; left: 40px; right: 40px;
    height: 1px; background: var(--rule);
  }
  .holder {
    position: absolute; left: 40px; top: 168px;
  }
  .holder__name {
    font-weight: 700; font-size: 21px; letter-spacing: .5px;
    text-transform: uppercase; color: var(--brand-blue);
  }
  .holder__name .surname { color: var(--brand-red); }
  .holder__title { font-size: 14px; color: var(--ink); margin-top: 1px; }
  .contact-list { list-style: none; margin-top: 12px; }
  .contact-list li {
    display: flex; align-items: center; gap: 7px;
    font-size: 14px; color: var(--ink); line-height: 20px;
  }
  .contact-list svg { width: 12px; height: 12px; fill: var(--brand-blue); flex: none; }
  /* Back */
  .card--back {
    background: var(--brand-blue);
    display: flex; align-items: center; justify-content: center; gap: 14px;
  }
  .card--back::after {
    content: ""; position: absolute; right: 0; top: 0; bottom: 0; width: 38%;
    background: var(--brand-red); z-index: 0;
  }
  .back-mark { position: relative; z-index: 1; display: flex; align-items: center; gap: 12px; }
  .back-mark__square { width: 30px; height: 30px; background: var(--white); }
  .back-mark__name {
    font-weight: 700; font-size: 26px; letter-spacing: 1px;
    color: var(--white); text-transform: uppercase; line-height: 1.15;
  }
</style>
</head>
<body>
<main class="card-set">
  <section class="card card--front">
    <div class="brand-lockup">
      <span class="brand-lockup__square"></span>
      <span class="brand-lockup__name">Velmora Freightway Solutions</span>
    </div>
    <div class="divider"></div>
    <div class="holder">
      <h1 class="holder__name">Dorian <span class="surname">Pike</span></h1>
      <p class="holder__title">CEO and Founder</p>
      <ul class="contact-list">
        <li>
          <svg viewBox="0 0 24 24" aria-hidden="true"><path d="M6.6 10.8a15.1 15.1 0 0 0 6.6 6.6l2.2-2.2a1 1 0 0 1 1-.25 11.4 11.4 0 0 0 3.6.57 1 1 0 0 1 1 1V20a1 1 0 0 1-1 1A17 17 0 0 1 3 4a1 1 0 0 1 1-1h3.5a1 1 0 0 1 1 1c0 1.25.2 2.45.57 3.57a1 1 0 0 1-.25 1z"/></svg>
          1-888-470-6158
        </li>
        <li>
          <svg viewBox="0 0 24 24" aria-hidden="true"><path d="M2 5h20v14H2zm2 2v.5l8 5 8-5V7l-8 5z"/></svg>
          dpike@vfwayroutes.com
        </li>
        <li>
          <svg viewBox="0 0 24 24" aria-hidden="true"><circle cx="12" cy="12" r="10"/></svg>
          www.vfwayroutes.com
        </li>
      </ul>
    </div>
  </section>

  <section class="card card--back">
    <div class="back-mark">
      <span class="back-mark__square"></span>
      <span class="back-mark__name">Velmora<br>Freightway<br>Solutions</span>
    </div>
  </section>
</main>
</body>
</html>
```